Retail Jewelry Business Card Design Project

We are in need of a new business card design for a retail jewelry store. This store is in the business of fine jewelry including but not specific to bridal jewelry, diamonds, designer jewelry and watches.

This store has been in business for 20 years but continues to strive for a modern professional appeal. The main colors use for this business are a royal blue, white and silver.

Target Market(s)

Target market is ages 18-50

Industry/Entity Type

Jewelry

Requirements
Must have
• Sales Person Name
Sales Person Email Address

Store Address
Store Phone
Website

Standard business card size. No odd shapes or sizes.
Nice to have
• Overall modern feel for card.

We have thought that a design with a nice feature of the logo on the back of the card would be nice but open to ideas.
Should not have
• No specific images of jewelry should be used.

```html
<!DOCTYPE html>
<html lang="en">
<head>
<meta charset="utf-8">
<title>Marlowe Grant Fine Jewelry – Business Cards</title>
<link rel="stylesheet" href="https://fonts.googleapis.com/css2?family=Cinzel:wght@400;600&display=swap">
<style>
  :root {
    --backdrop: #2b1810;
    --card-white: #ffffff;
    --card-white-shade: #ededf0;
    --royal: #2e2f93;
    --royal-light: #3a3ca3;
    --royal-deep: #2a2b8a;
    --rule-lilac: #7d72c4;
    --on-royal: #ffffff;
  }
  * { margin: 0; padding: 0; box-sizing: border-box; }
  html, body {
    width: 1200px;
    height: 1000px;
    overflow: hidden;
    background: var(--backdrop);
    font-family: "Cinzel", "Times New Roman", serif;
  }
  .canvas {
    position: relative;
    width: 1200px;
    height: 1000px;
  }
  .card {
    position: absolute;
    width: 610px;
    height: 350px;
    box-shadow: 0 10px 28px rgba(0, 0, 0, 0.55);
  }
  .card--front {
    left: 120px;
    top: 105px;
    background: linear-gradient(170deg, var(--card-white) 55%, var(--card-white-shade) 100%);
    color: var(--royal);
  }
  .card--back {
    left: 465px;
    top: 540px;
    background: linear-gradient(180deg, var(--royal-light) 0%, var(--royal) 50%, var(--royal-deep) 100%);
    color: var(--on-royal);
  }
  .brand {
    position: absolute;
    left: 34px;
    top: 46px;
    width: 290px;
  }
  .brand__name {
    display: block;
    font-weight: 600;
    font-size: 25px;
    letter-spacing: 1.5px;
    line-height: 1.2;
    padding-bottom: 6px;
    border-bottom: 2px solid currentColor;
  }
  .card--front .brand__name { border-bottom-color: var(--rule-lilac); }
  .brand__tag {
    display: block;
    text-align: center;
    font-weight: 600;
    font-size: 17px;
    letter-spacing: 2px;
    margin-top: 4px;
  }
  .contact {
    position: absolute;
    left: 38px;
    font-variant: small-caps;
  }
  .card--front .contact { top: 240px; }
  .card--back .contact { top: 196px; }
  .contact__person {
    font-size: 22px;
    letter-spacing: 0.5px;
  }
  .contact__email {
    font-size: 14px;
    letter-spacing: 0.5px;
    margin-top: 6px;
  }
  .contact__line {
    font-size: 17px;
    line-height: 1.45;
    letter-spacing: 0.3px;
  }
</style>
</head>
<body>
  <main class="canvas">
    <section class="card card--front" aria-label="Business card front">
      <div class="brand">
        <span class="brand__name">Marlowe Grant</span>
        <span class="brand__tag">FINE JEWELRY</span>
      </div>
      <div class="contact">
        <p class="contact__person">Marlowe Grant Ellison</p>
        <p class="contact__email">marlowe@marlowegrantjewelry.com</p>
      </div>
    </section>

    <section class="card card--back" aria-label="Business card back">
      <div class="brand">
        <span class="brand__name">Marlowe Grant</span>
        <span class="brand__tag">FINE JEWELRY</span>
      </div>
      <div class="contact">
        <p class="contact__line">Marlowe Grant Fine</p>
        <p class="contact__line">2280 Linden Avenue</p>
        <p class="contact__line">Bay Harbor, FL 32490</p>
        <p class="contact__line">www.marlowegrantjewelry.com</p>
      </div>
    </section>
  </main>
</body>
</html>
```